New Business Card Design Project LORVANTI-Italy

we are LORVANTI-Italy
our company in the market for 3 years we are luxury cosmetic company and its about time for a facelift :)
i will like to have elegant luxurious and unique business card
that will give the person that get it a unique, luxurious and elegant impression
I'm VERY OPEN FOR NEW IDEAS , even duo i add a few files of things that i see on line and i like them

i add my logo as well
my website is LORVANTI.COM
(if you would like to see the main style that we have)

Target Market(s)

adult that have money :)

Industry/Entity Type

Business

Contact Information for Business Card

Name - Dario Lorvanti
Position - CEO and CO Founder
address - 4817 E Halvern
telephone - 555-384-1926
email - dario@lorvanti.com
fax - 555-384-1926
website - LORVANTI.COM

Colors
000000
959595
fbee3e
ffffff

Requirements
Must have
• big logo in GOLD color
• elegant look
• impressive
Nice to have
• not must but maybe classy pattern background
• not must but maybe emblem
• maybe clear plastic business card
Should not have
• colors
• images

```html
<!DOCTYPE html>
<html lang="en">
<head>
<meta charset="utf-8">
<title>LORVANTI-Italy Business Card</title>
<link href="https://fonts.googleapis.com/css2?family=Oswald:wght@500&family=Open+Sans:wght@400;600&display=swap" rel="stylesheet">
<style>
  :root {
    --backdrop: #1b1b1b;
    --card-black: #0d0d0d;
    --card-white: #ffffff;
    --ink-dark: #3f3f3f;
    --ink-grey: #7a7a7a;
    --silver: #a4a4a4;
    --gold: #c9a227;
  }
  * { margin: 0; padding: 0; box-sizing: border-box; }
  html, body {
    width: 1200px; height: 833px; overflow: hidden;
    background: var(--backdrop);
  }
  .stage {
    position: relative; width: 1200px; height: 833px;
    display: flex; align-items: center; justify-content: center; gap: 40px;
  }
  .card {
    position: relative; width: 520px; height: 297px;
    box-shadow: 0 10px 30px rgba(0,0,0,.5);
  }
  /* front */
  .card-front { background: var(--card-black); }
  .brand-mark {
    position: absolute; left: 0; right: 0; top: 72px;
    display: flex; flex-direction: column; align-items: center; gap: 18px;
  }
  .brand-disc {
    width: 76px; height: 76px; border-radius: 50%;
    border: 2px solid var(--silver);
  }
  .brand-name {
    font-family: "Open Sans", sans-serif; font-weight: 600;
    font-size: 38px; letter-spacing: 6px; color: var(--silver);
  }
  /* back */
  .card-back { background: var(--card-white); }
  .identity {
    position: absolute; right: 268px; top: 104px; text-align: right;
  }
  .person-name {
    font-family: "Oswald", sans-serif; font-weight: 500;
    font-size: 33px; line-height: 1; color: var(--ink-dark);
    text-transform: uppercase; letter-spacing: .5px;
  }
  .person-role {
    font-family: "Open Sans", sans-serif; font-size: 13px;
    color: var(--gold); margin-top: 4px;
  }
  .divider {
    position: absolute; left: 268px; top: 96px; width: 2px; height: 80px;
    background: var(--gold);
  }
  .contact-list {
    position: absolute; left: 286px; top: 98px; list-style: none;
    font-family: "Open Sans", sans-serif; font-size: 13px; color: var(--ink-grey);
  }
  .contact-list li {
    display: flex; align-items: center; gap: 8px; height: 19px;
  }
  .contact-list svg { width: 12px; height: 12px; fill: var(--gold); flex: none; }
  .address-line {
    position: absolute; left: 70px; bottom: 40px;
    font-family: "Open Sans", sans-serif; font-size: 13px; color: var(--ink-grey);
  }
  .address-line .company { color: var(--gold); font-weight: 600; }
</style>
</head>
<body>
<main class="stage">
  <section class="card card-front" aria-label="Card front">
    <div class="brand-mark">
      <div class="brand-disc"></div>
      <div class="brand-name">LORVANTI</div>
    </div>
  </section>

  <section class="card card-back" aria-label="Card back">
    <div class="identity">
      <div class="person-name">Dario Lorvanti</div>
      <div class="person-role">CEO and CO Founder</div>
    </div>
    <div class="divider"></div>
    <ul class="contact-list">
      <li>
        <svg viewBox="0 0 24 24"><path d="M6.6 10.8a15 15 0 0 0 6.6 6.6l2.2-2.2a1 1 0 0 1 1-.25 11.4 11.4 0 0 0 3.6.57 1 1 0 0 1 1 1V20a1 1 0 0 1-1 1A17 17 0 0 1 3 4a1 1 0 0 1 1-1h3.5a1 1 0 0 1 1 1c0 1.25.2 2.45.57 3.57a1 1 0 0 1-.25 1z"/></svg>
        555-384-1926
      </li>
      <li>
        <svg viewBox="0 0 24 24"><path d="M6 2h12v6H6zM3 9h18a1 1 0 0 1 1 1v7h-4v5H6v-5H2v-7a1 1 0 0 1 1-1zm5 8v3h8v-3z"/></svg>
        555-384-1926
      </li>
      <li>
        <svg viewBox="0 0 24 24"><path d="M2 5h20v14H2zm2 2v.5l8 5 8-5V7l-8 5z"/></svg>
        dario@lorvanti.com
      </li>
      <li>
        <svg viewBox="0 0 24 24"><path d="M12 2a10 10 0 1 0 0 20 10 10 0 0 0 0-20zm0 2c1 1.3 1.8 3 2.1 5H9.9C10.2 7 11 5.3 12 4zM4.3 13h3.6a15 15 0 0 0 0-2H4.3a8 8 0 0 0 0 2zm5.6 0h4.2a13 13 0 0 0 0-2H9.9a13 13 0 0 0 0 2zm6.2 0h3.6a8 8 0 0 0 0-2h-3.6a15 15 0 0 1 0 2zM12 20c-1-1.3-1.8-3-2.1-5h4.2c-.3 2-1.1 3.7-2.1 5z"/></svg>
        LORVANTI.COM
      </li>
    </ul>
    <p class="address-line"><span class="company">LORVANTI-Italy</span> - 4817 E Halvern</p>
  </section>
</main>
</body>
</html>
```